Kestrel Facilities Business Card Design

We would now like to design business cards with the new Kestrel Facilities logo

Target Market(s)

Professional

Industry/Entity Type

Professional services

Contact Information for Business Card

Employee name, title, phone number, email address, corporate office address and logo.

Font styles to use
Sans Serif

Colors
0054AA
0677BA
7BADD7
CADEEF
E8F1F8

Requirements
Must have
• My logo
Should not have
• any other pictures or images besides my logo

```html
<!DOCTYPE html>
<html lang="en">
<head>
<meta charset="utf-8">
<title>Kestrel Facilities – Business Card</title>
<link href="https://fonts.googleapis.com/css2?family=Montserrat:wght@400;500;700&display=swap" rel="stylesheet">
<style>
  :root {
    --brand-blue: #3579c3;
    --ink: #1d1d1f;
    --paper: #ffffff;
    --backdrop: #9a9a9a;
  }
  * { margin: 0; padding: 0; box-sizing: border-box; }
  html, body { width: 1200px; height: 900px; overflow: hidden; }
  body {
    background: var(--backdrop);
    font-family: "Montserrat", sans-serif;
    position: relative;
  }
  .card {
    position: absolute;
    left: 285px;
    width: 630px;
    height: 360px;
    background: var(--paper);
    border-radius: 28px;
    overflow: hidden;
  }
  .card--back { top: 60px; }
  .card--front { top: 480px; }

  .wordmark {
    display: flex;
    align-items: center;
    gap: 14px;
    color: var(--brand-blue);
    font-weight: 700;
    text-transform: uppercase;
    letter-spacing: 2px;
  }
  .wordmark__square {
    background: var(--brand-blue);
    flex: none;
  }
  .card--back .wordmark {
    position: absolute;
    left: 0; right: 0; top: 0; bottom: 0;
    justify-content: center;
    font-size: 34px;
  }
  .card--back .wordmark__square { width: 40px; height: 40px; }

  .card--front .wordmark {
    position: absolute;
    left: 160px;
    top: 54px;
    font-size: 26px;
  }
  .card--front .wordmark__square { width: 30px; height: 30px; }

  .swoosh { position: absolute; left: 0; top: 0; width: 630px; height: 360px; }

  .identity {
    position: absolute;
    right: 372px;
    top: 138px;
    text-align: right;
  }
  .identity__name {
    color: var(--brand-blue);
    font-weight: 700;
    font-size: 24px;
    letter-spacing: 0.5px;
    white-space: nowrap;
  }
  .identity__title {
    color: var(--ink);
    font-size: 16px;
    margin-top: 4px;
  }
  .divider {
    position: absolute;
    left: 276px;
    top: 124px;
    width: 2px;
    height: 78px;
    background: var(--brand-blue);
  }
  .contacts {
    position: absolute;
    left: 294px;
    top: 120px;
    list-style: none;
  }
  .contacts li {
    display: flex;
    align-items: center;
    gap: 8px;
    font-size: 15px;
    color: var(--ink);
    line-height: 28px;
    white-space: nowrap;
  }
  .contacts svg { width: 16px; height: 16px; fill: var(--brand-blue); flex: none; }
  .address {
    position: absolute;
    left: 56px;
    top: 224px;
    font-size: 15px;
    color: var(--ink);
    white-space: nowrap;
  }
</style>
</head>
<body>

<section class="card card--back" aria-label="Business card back">
  <div class="wordmark"><span class="wordmark__square"></span><span>Kestrel Facilities</span></div>
</section>

<section class="card card--front" aria-label="Business card front">
  <svg class="swoosh" viewBox="0 0 630 360" aria-hidden="true">
    <path d="M0,330 C370,328 600,266 632,96 L632,362 L0,362 Z" fill="var(--brand-blue)"/>
    <path d="M0,312 C360,310 590,250 626,52" fill="none" stroke="var(--brand-blue)" stroke-width="5"/>
  </svg>

  <div class="wordmark"><span class="wordmark__square"></span><span>Kestrel Facilities</span></div>

  <div class="identity">
    <div class="identity__name">DANA WHITFIELD</div>
    <div class="identity__title">Co-Founder</div>
  </div>

  <div class="divider"></div>

  <ul class="contacts">
    <li>
      <svg viewBox="0 0 24 24"><path d="M6.6 10.8a15.1 15.1 0 0 0 6.6 6.6l2.2-2.2c.3-.3.7-.4 1-.2 1.1.4 2.3.6 3.6.6.6 0 1 .4 1 1V20c0 .6-.4 1-1 1A17 17 0 0 1 3 4c0-.6.4-1 1-1h3.5c.6 0 1 .4 1 1 0 1.3.2 2.5.6 3.6.1.3 0 .7-.2 1z"/></svg>
      +254-160-47215
    </li>
    <li>
      <svg viewBox="0 0 24 24"><path d="M2 5h20v14H2zm2 2v.5l8 5 8-5V7l-8 5z"/></svg>
      info@kestrelfm.com
    </li>
    <li>
      <svg viewBox="0 0 24 24"><circle cx="12" cy="12" r="10"/></svg>
      www.kestrelfm.com
    </li>
  </ul>

  <p class="address">4180 N. Harbor Lane Suite 210 Norvale 32</p>
</section>

</body>
</html>
```